Dunfield Inc 1 pg brochure for entrepreneurs

We need a one page brochure (2 sided) designed for a finance and strategy consulting company called Dunfield Inc. which does work in Canada and the United States currently. This company works with entrepreneurs, helping them to establish finance operations, evaluate their financial infomation and apply insight from it to business strategies. Essentially we help entrepreneurs grow their business ... we take care of their finance needs and give them sound business advice ... allowing them to focus on their core business and business strategy.

This one page brochure is meant to caputure what services we provide but also positon that we are also entrepreneurs and we understand how entrepreneurs think .... we not only bring technical competence but cultural insight in this regard as well. We understand how nimble and stealth an entrepreneur's business is so we don't gouge them with expensive consulting fees. We don't want to look like a massive corporation ...we want to look professional, smart and reliable. We want to reflect that we are entrepreneural ourselves even in fact that we have a niche offering that is totally targeted to businesses of this nature.

Major emphasis points for the piece are
1) our core values, this could be a side bar or box
2) the credentials of our founder, he is technically competent and an entrepreneur himself (we have his picture to include)
3) our offerings, what we can do for a company, the client quotes provided are a good illustration of what we offer, the relief we provide a client and of what value we provide - make sure you read these, this could also be a side bar or box, some kind of special call out so the service offerings are very clear

The brochure needs to be editable, so in a format that we can work with it for future, if we need to make updates, one that we can use in Microsoft word and convert to a PDF format. It will be emailed to people (in pdf) and also brought to meetings.

We have a new logo and this design should be an extenstion of it from a colour, look and feel perspective. The piece should also be clean and not too copy heavy so we encourage use of sub-heads, whitespace, etc.

When we send this piece out or hand it to someone, the impression should be "I am comfortable with Dunfield Inc. they can help me and are people who get me, people I can trust to work closely with me on my business who are personally vested in my success".

Hello all, thank you for sumitting designs, there is some great work here.  A few changes/requests ...

Pls add the following headline on the front page right off the top

Entrepreneurs helping entrepreneurs, providing strategic financial services

Can we put Services on the front page? and call them out with treatment in a text box or with something strong that creates emphasis

Can the quote pls be broken up as opposed to one long list of 6 quotes? They can be floated throughout the piece, we can use less of them (or not) and put them on the front and back of the brochure? 

Also looking for the final product to be a little more bold in colour ...

Thx all, let us know if you have questions

Target Market(s)

Individuals (CEO) who runs their own established, yet growing business, who needs a business-minded CFO

Industry/Entity Type

Financial

Requirements
Must have
• Must have photo of founder, include his name and credentials under photo
All copy provide must be included
If not sure of a headline put in dummy text and we will provide headline or sub head copy
Should not have
• Fonts to be clean, no serif fonts. Should compliment logo, not the same font exactly but easily replicable in Microsoft Word and complimentary
No illustrations or cliche clip art

```html
<!DOCTYPE html>
<html lang="en">
<head>
<meta charset="utf-8">
<title>Dunfield Inc — Brochure</title>
<link href="https://fonts.googleapis.com/css2?family=Arimo:ital,wght@0,400;0,700;1,400&family=Roboto:wght@300&display=swap" rel="stylesheet">
<style>
:root{
  --stage:#231f20;
  --paper:#ffffff;
  --navy:#2d2a6b;
  --ink:#4d4d4f;
  --brand-blue:#1b75bb;
  --accent-cyan:#2bb9dc;
  --services-bg:#d5ebf6;
  --panel-grey:#e6e7e8;
  --rule:#6d6e71;
}
*{margin:0;padding:0;box-sizing:border-box}
html,body{width:1200px;height:835px;overflow:hidden;background:var(--stage)}
body{font-family:"Arimo",Arial,sans-serif;color:var(--ink);position:relative}
.page{position:absolute;top:61px;width:543px;height:702px;background:var(--paper)}
.page--front{left:49px}
.page--back{left:608px}
.abs{position:absolute}

/* header */
.brand-square{left:46px;top:26px;width:40px;height:40px;background:var(--brand-blue)}
.brand-name{left:96px;top:33px;font-size:24px;font-weight:400;color:var(--navy)}
.contact{top:31px;font-size:10px;line-height:15px;color:#414042}
.contact b{font-weight:700;color:#231f20;margin-right:3px}
.header-rule{left:43px;top:88px;width:457px;height:1px;background:var(--rule)}

/* headline */
.headline{left:43px;top:109px;font-family:"Roboto",Arial,sans-serif;font-weight:300;font-size:37px;line-height:46px;color:var(--navy)}
.subhead{left:43px;top:258px;font-size:15.5px;font-weight:700;color:var(--navy)}
.intro{left:43px;top:290px;width:272px;font-size:9.8px;line-height:14.3px}

/* tabs */
.tab{height:21px;background:var(--brand-blue);color:#fff;font-size:13px;line-height:21px;padding-left:7px;font-weight:400}
.tab::after{content:"";position:absolute;right:0;top:0;border-top:21px solid transparent;border-right:14px solid var(--accent-cyan)}
.tab--dark::after{border-right-color:var(--navy)}

.about{left:43px;top:410px;width:283px;font-size:8.6px;line-height:13.3px}
.founder-photo{left:43px;top:475px;width:113px;height:152px;background:linear-gradient(160deg,#5b5e66,#2a2b30 70%,#15161a)}
.about-wrap{left:169px;top:463px;width:155px;font-size:8.6px;line-height:13.3px}
.founder-name{left:169px;top:609px;font-size:8.6px;color:#231f20}
.founder-role{left:169px;top:622px;font-size:6.5px}

/* services */
.services{left:345px;top:116px;width:155px;height:350px;background:var(--services-bg);border-radius:7px}
.services-list{left:355px;top:147px;width:140px;list-style:none;font-size:9.8px;line-height:12.3px;color:#231f20}
.services-list li{position:relative;padding-left:13px;margin-bottom:9px}
.services-list svg{position:absolute;left:0;top:2px}

.quote-card{left:345px;width:155px;background:var(--panel-grey);border-radius:7px;padding:10px 12px;font-style:italic;font-size:7.8px;line-height:12.3px}

.site-url{right:43px;top:657px;font-family:"Roboto",Arial,sans-serif;font-size:18px;font-weight:300;color:var(--navy)}
.footer-rule{left:43px;top:681px;width:457px;height:1px;background:#231f20}

/* back */
.hero-image{left:45px;top:61px;width:256px;height:156px;background:linear-gradient(120deg,#0d1b3a,#1d4f8c 55%,#3c8fd0)}
.bio{left:48px;top:223px;width:262px;font-size:8.6px;line-height:13.3px}
.bio p+p{margin-top:13.3px}

.values{left:334px;top:78px;width:178px;height:397px;background:var(--panel-grey)}
.values-list{left:349px;top:112px;width:145px;list-style:none;font-size:9.8px;line-height:12.4px;color:#231f20}
.values-list li{position:relative;padding-left:15px;margin-bottom:10px}
.values-list li::before{content:"";position:absolute;left:0;top:3px;width:6px;height:6px;background:var(--brand-blue)}

.testimonials{left:32px;top:519px;width:479px;height:115px;background:var(--accent-cyan)}
.t-quote{color:#fff;font-style:italic;font-size:7.8px;line-height:12.3px}
.t-divider{width:1px;background:rgba(255,255,255,.55)}
</style>
</head>
<body>

<section class="page page--front">
  <div class="abs brand-square" aria-hidden="true"></div>
  <div class="abs brand-name">Dunfield Inc</div>
  <address class="abs contact" style="left:279px;font-style:normal">1180 9 Avenue SW,<br>Calgary Alberta,<br>Canada, T2R 0A1</address>
  <div class="abs contact" style="left:388px"><b>P</b> 03.555.0142<br><b>F</b> 000 000 000<br><b>E</b> grant@dunfieldinc.ca</div>
  <div class="abs header-rule"></div>

  <h1 class="abs headline">Entrepreneurs<br>helping<br>entrepreneurs,</h1>
  <h2 class="abs subhead">providing strategic financial services</h2>
  <p class="abs intro">By engaging Dunfield Inc, entrepreneurs can regularly access senior executive financial acumen and strategic discipline without having to hire a full-time financial executive or overspend on third-party service providers who are transactional in nature.</p>

  <h3 class="abs tab" style="left:43px;top:375px;width:120px">Who we are?</h3>
  <p class="abs about">Dunfield Inc. evolved out of the companies, partnerships and relationships that Grant Holloway, its founder, has nurtured and built over the last 22 years. Mr. Holloway, the founder of Dunfield, is an entrepreneur himself having built his own companies and managed</p>
  <div class="abs founder-photo" role="img" aria-label="Portrait photo of founder Grant Holloway"></div>
  <div class="abs about-wrap">
    <p>several successful investment funds whose mandates were to invest in entrepreneurial growth companies.</p>
    <p style="margin-top:13px">Over his career, he has worked extensively with entrepreneurs like himself who have struggled to build an experienced and engaged executive management team.</p>
  </div>
  <div class="abs founder-name">Grant Holloway,</div>
  <div class="abs founder-role">Founder</div>

  <div class="abs services"></div>
  <h3 class="abs tab" style="left:355px;top:107px;width:121px">Services</h3>
  <ul class="abs services-list">
    <li><svg width="10" height="9" viewBox="0 0 10 9"><path d="M1 5l3 3 5-7" fill="none" stroke="#1b75bb" stroke-width="1.6"/></svg>We work intimately with our clients to determine their corporate and personal objectives</li>
    <li><svg width="10" height="9" viewBox="0 0 10 9"><path d="M1 5l3 3 5-7" fill="none" stroke="#1b75bb" stroke-width="1.6"/></svg>We evaluate corporate strategies and assist in aligning them with financial ones</li>
    <li><svg width="10" height="9" viewBox="0 0 10 9"><path d="M1 5l3 3 5-7" fill="none" stroke="#1b75bb" stroke-width="1.6"/></svg>We assist in budgeting, investing, financial forecasting and analysis and asset management</li>
    <li><svg width="10" height="9" viewBox="0 0 10 9"><path d="M1 5l3 3 5-7" fill="none" stroke="#1b75bb" stroke-width="1.6"/></svg>We develop and implement accountability financial systems, processes and reporting</li>
    <li><svg width="10" height="9" viewBox="0 0 10 9"><path d="M1 5l3 3 5-7" fill="none" stroke="#1b75bb" stroke-width="1.6"/></svg>We manage capital raising efforts, tax structuring issues and corporate transactions including mergers, acquisitions, and the sale of your business</li>
  </ul>

  <blockquote class="abs quote-card" style="top:479px;height:93px">“I need a financial executive who gets the numbers, can think strategically and translate that combined expertise and understanding into forward-looking corporate strategies” powerful</blockquote>
  <blockquote class="abs quote-card" style="top:586px;height:52px">“I need a financial executive who understands the inherent makeup of an entrepreneur”</blockquote>

  <div class="abs site-url">www.dunfieldinc.ca</div>
  <div class="abs footer-rule"></div>
</section>

<section class="page page--back">
  <div class="abs hero-image" role="img" aria-label="Photo of a businessman writing strategy words on a glass screen"></div>
  <div class="abs bio">
    <p>Mr. Holloway has a proven track record of developing and implementing strategic corporate policy. His experience and education is in corporate finance, portfolio management and building businesses and he is a registered Portfolio Manager. He also has earned an MBA from the University of Westbrook (1995) and is a Chartered Financial Analyst (CFA, 1999).</p>
    <p>He applies this competence to evaluating an entrepreneur's vision and corporate strategies and assisting in translating them into higher growth, improved efficiency and higher profitability. He has extensive experience in public and private, debt and equity capital markets, involving raising, managing and investing capital and completing corporate transactions. He has evaluated hundreds of corporate business strategies for potential investment.</p>
    <p>Other core skills include financial and tax analysis, working with high-performing investment teams, managing financial and accounting functions, designing and implementing operational and compliance systems.</p>
  </div>

  <div class="abs values"></div>
  <h3 class="abs tab tab--dark" style="left:349px;top:67px;width:137px;height:23px;line-height:23px;font-size:14px">Core Values</h3>
  <ul class="abs values-list">
    <li>We love working with entrepreneurs because they like adventure. We understand the high energy, creativity and passion required to take high risks and achieve a corporate vision.</li>
    <li>We like entrepreneurs because they are focused on achievement. They are “can-do” people who take action.</li>
    <li>We like entrepreneurs because their business relationships are like family. Entrepreneurs are personally invested and value personal relationships with amazing people.</li>
    <li>We like entrepreneurs because they work hard and live well. Health and wellness is as important as financial success, and most of all having fun is central to the mind set of most successful entrepreneurs.</li>
  </ul>

  <div class="abs testimonials"></div>
  <h3 class="abs tab tab--dark" style="left:44px;top:507px;width:121px;height:22px;line-height:22px;font-size:14px">Testimonials</h3>
  <p class="abs t-quote" style="left:56px;top:540px;width:133px">“I need a financial executive who gets the numbers, can think strategically and translate that combined expertise and understanding into forward-looking corporate strategies” powerful</p>
  <div class="abs t-divider" style="left:207px;top:532px;height:44px"></div>
  <p class="abs t-quote" style="left:217px;top:532px;width:118px">“I need a financial executive who understands the inherent makeup of an entrepreneur”</p>
  <div class="abs t-divider" style="left:339px;top:532px;height:44px"></div>
  <p class="abs t-quote" style="left:346px;top:532px;width:152px">“If I could hire my equal in a financial capacity, my executive team would be complete” <span style="float:right">grant's fave</span></p>
  <p class="abs t-quote" style="left:217px;top:595px;width:290px">“I need help implementing better financial systems and process that can be maintained in a disciplined way”</p>

  <div class="abs site-url">www.dunfieldinc.ca</div>
  <div class="abs footer-rule"></div>
</section>

</body>
</html>
```